Tidewell Homecare

I am looking to have a website designed for a housekeeping company that looks similar to this one. https://marloweshomecare.example/

I need 5 websites designed but will start with this one to see how I like it.

Industry/Entity Type

House Cleaning

Coding

Coded - Design and coding required

Number of Pages Required

5+ page

Font styles to use
Serif
Script

Colors
ffffff
fdf9cf
fbf289
fbee3f
d6edf3
86cae7
33a6d7
edf1f8
cedeed

```html
<!DOCTYPE html>
<html lang="en">
<head>
<meta charset="utf-8">
<title>About Us – Tidewell Homecare</title>
<link href="https://fonts.googleapis.com/css2?family=Oswald:wght@400&family=Poppins:wght@400;500&display=swap" rel="stylesheet">
<style>
  :root{
    --blue:#0aa0e6;
    --blue-deep:#0a84c8;
    --ink:#111111;
    --text:#666666;
    --nav:#555555;
    --dark:#282828;
    --muted:#9a9a9a;
    --white:#ffffff;
  }
  *{margin:0;padding:0;box-sizing:border-box}
  html,body{width:1200px;height:1194px;overflow:hidden;background:var(--white)}
  body{position:relative;font-family:"Poppins",sans-serif;color:var(--text)}
  .abs{position:absolute}
  .site-header{position:absolute;left:0;top:0;width:1200px;height:83px;background:var(--white);z-index:3}
  .brand{position:absolute;left:161px;top:12px;font-family:"Oswald",sans-serif;font-weight:400;color:var(--ink);font-size:28px;line-height:30px;text-transform:uppercase;letter-spacing:1px}
  .main-nav{position:absolute;top:32px;left:460px;display:flex;gap:0}
  .main-nav a{position:absolute;white-space:nowrap;font-size:12px;font-weight:500;color:var(--nav);text-decoration:none;text-transform:uppercase}
  .main-nav a.is-current{color:var(--blue)}
  .call-btn{position:absolute;left:873px;top:20px;width:165px;height:41px;border-radius:21px;background:linear-gradient(90deg,var(--blue-deep),var(--blue));display:flex;align-items:center;justify-content:center;gap:8px;color:var(--white);font-family:"Oswald",sans-serif;font-size:18px}
  .hero{position:absolute;left:0;top:83px;width:1200px;height:422px}
  .hero-title{position:absolute;left:0;top:188px;width:1200px;text-align:center;font-family:"Oswald",sans-serif;font-weight:400;font-size:62px;color:#2a2a2a;line-height:72px}
  .about-copy{position:absolute;left:275px;top:569px;width:650px;text-align:center;font-size:11px;line-height:19.5px;color:var(--text)}
  .about-copy p+p{margin-top:19.5px}
  .cta{position:absolute;left:515px;top:823px;width:139px;height:38px;border-radius:19px;background:linear-gradient(90deg,var(--blue-deep),var(--blue));color:var(--white);font-family:"Oswald",sans-serif;font-size:16px;display:flex;align-items:center;justify-content:center;text-decoration:none}
  .footer-bg{position:absolute;left:0;top:880px}
  .footer-brand{position:absolute;left:161px;top:1057px;font-family:"Oswald",sans-serif;font-weight:400;color:var(--white);font-size:28px;line-height:30px;text-transform:uppercase;letter-spacing:1px}
  .copyright{position:absolute;left:163px;top:1132px;width:200px;font-size:11px;line-height:16.5px;color:var(--muted)}
  .copyright span{color:var(--white)}
  .footer-links{position:absolute;left:391px;top:1049px;list-style:none}
  .footer-links li{height:26px;font-size:11px;color:var(--muted)}
  .footer-links li.is-current{color:var(--blue)}
  .footer-phone{position:absolute;left:642px;top:1034px;font-family:"Oswald",sans-serif;font-size:20px;color:var(--white)}
  .footer-mail{position:absolute;left:637px;top:1084px;font-size:11px;color:var(--muted)}
  .social{position:absolute;top:1051px;width:34px;height:34px;border-radius:50%;background:var(--white)}
  .social.is-primary{background:var(--blue)}
</style>
</head>
<body>

<header class="site-header">
  <div class="brand">Tidewell<br>Homecare</div>
  <nav class="main-nav">
    <a style="left:0">Home</a>
    <a style="left:66px">Service</a>
    <a style="left:143px">Pricing</a>
    <a style="left:221px" class="is-current">About Us</a>
    <a style="left:308px">Contact Us</a>
  </nav>
  <div class="call-btn">
    <svg width="15" height="15" viewBox="0 0 24 24"><path fill="#fff" d="M6.6 10.8a15.1 15.1 0 0 0 6.6 6.6l2.2-2.2a1 1 0 0 1 1-.25 11.4 11.4 0 0 0 3.6.57 1 1 0 0 1 1 1V20a1 1 0 0 1-1 1A17 17 0 0 1 3 4a1 1 0 0 1 1-1h3.5a1 1 0 0 1 1 1c0 1.25.2 2.45.57 3.57a1 1 0 0 1-.25 1z"/></svg>
    555 014 2290
  </div>
</header>

<section class="hero">
  <svg width="1200" height="422" viewBox="0 0 1200 422" class="abs" style="left:0;top:0">
    <defs>
      <linearGradient id="roomTone" x1="0" y1="0" x2="1" y2="1">
        <stop offset="0" stop-color="#e6e9ef"/>
        <stop offset="0.5" stop-color="#e9e2d8"/>
        <stop offset="1" stop-color="#d8dbe2"/>
      </linearGradient>
      <linearGradient id="waveBlue" x1="0" y1="0" x2="1" y2="0">
        <stop offset="0" stop-color="#0a84c8"/>
        <stop offset="1" stop-color="#0aa8f0"/>
      </linearGradient>
    </defs>
    <rect width="1200" height="422" fill="url(#roomTone)" role="img" aria-label="Bright modern living room and kitchen interior with a round dining table"/>
    <path d="M0,338 C150,420 300,430 450,405 C650,370 750,290 950,280 C1080,275 1160,320 1200,345 L1200,422 L0,422Z" fill="url(#waveBlue)"/>
    <path d="M0,360 C150,432 300,442 450,420 C650,388 760,306 950,300 C1080,296 1160,340 1200,372 L1200,422 L0,422Z" fill="#fff"/>
  </svg>
  <h1 class="hero-title">About Us</h1>
</section>

<main class="about-copy">
  <p>Our goal at Tidewell Homecare is very straight forward -To help you live a better, cleaner life with less stress. To provide you with peace of mind knowing your property is clean.</p>
  <p>When your house is regularly cleaned and inspected, small home management issues stay small, and sometimes our intervention makes professional repair unnecessary.&nbsp; You can rest easy when you know the minute you walk out the door, the property will be perfectly cleaned and fresh, ready for your arrival.</p>
  <p>Tidewell Homecare was created at the request of real estate clients who needed professional attention to their vacation and second homes while they were away.&nbsp; After years of managing Vacation Rental properties and having sublevel housekeeping services, we finally came to the realization, the only to get things done right was to do it ourselves.&nbsp; Tidewell Homecare was then formed and has been successful since its inception.</p>
</main>
<a class="cta">CONTACT US</a>

<footer>
  <svg class="footer-bg" width="1200" height="314" viewBox="0 0 1200 314">
    <path d="M0,43 C150,120 300,135 450,118 C650,95 780,15 950,5 C1080,0 1160,40 1200,75 L1200,314 L0,314Z" fill="#282828"/>
  </svg>
  <div class="footer-brand">Tidewell<br>Homecare</div>
  <p class="copyright">© <span>Tidewell Homecare</span> - 2020. All Right Reserved.</p>
  <ul class="footer-links">
    <li class="is-current">Home</li>
    <li>Service Offered</li>
    <li>About Us</li>
    <li>Contact Us</li>
  </ul>
  <svg class="abs" style="left:616px;top:1053px" width="20" height="20" viewBox="0 0 24 24"><path fill="#fff" d="M6.6 10.8a15.1 15.1 0 0 0 6.6 6.6l2.2-2.2a1 1 0 0 1 1-.25 11.4 11.4 0 0 0 3.6.57 1 1 0 0 1 1 1V20a1 1 0 0 1-1 1A17 17 0 0 1 3 4a1 1 0 0 1 1-1h3.5a1 1 0 0 1 1 1c0 1.25.2 2.45.57 3.57a1 1 0 0 1-.25 1z"/></svg>
  <div class="footer-phone">555 014 2290</div>
  <svg class="abs" style="left:616px;top:1093px" width="16" height="13" viewBox="0 0 16 13"><rect x="0.75" y="0.75" width="14.5" height="11.5" rx="1.5" fill="none" stroke="#9a9a9a" stroke-width="1.3"/><path d="M1 1.5 L8 7 L15 1.5" fill="none" stroke="#9a9a9a" stroke-width="1.3"/></svg>
  <div class="footer-mail">info@tidewellhomecare.example</div>
  <span class="social is-primary" style="left:870px"></span>
  <span class="social" style="left:915px"></span>
  <span class="social" style="left:960px"></span>
  <span class="social" style="left:1005px"></span>
</footer>

</body>
</html>
```